VOMRA Pty Ltd Business Card

Looking for a simple yet eye-catching double-sided business card design using my company logo on one side and contact details on the other.

Target Market(s)

Government

Industry/Entity Type

Communication Systems Engineering

Contact Information for Business Card

VOMRA Pty Ltd

Requirements
Nice to have
• Would be great to have a QR code so details can be scanned into contacts

```html
<!DOCTYPE html>
<html lang="en">
<head>
<meta charset="utf-8">
<title>VOMRA Pty Ltd Business Card</title>
<link rel="stylesheet" href="https://fonts.googleapis.com/css2?family=Lato:wght@400;700;900&display=swap">
<style>
  :root {
    --stage: #79b6f1;
    --card-light: #ffffff;
    --card-dark: #2d2d2d;
    --ink: #2b2b2b;
    --ink-soft: #555555;
    --brand-ink: #393e44;
    --white: #ffffff;
  }
  * { box-sizing: border-box; margin: 0; padding: 0; }
  html, body { width: 1200px; height: 1200px; overflow: hidden; }
  body {
    background: var(--stage);
    font-family: "Lato", Arial, sans-serif;
    position: relative;
  }
  .card {
    position: absolute;
    left: 173px;
    width: 854px;
    height: 512px;
    box-shadow: 0 18px 40px rgba(20, 50, 90, 0.35);
    overflow: hidden;
  }
  .card--front { top: 70px; background: var(--card-light); }
  .card--back { top: 624px; background: var(--card-dark); }

  /* Front */
  .brand-name {
    position: absolute;
    font-weight: 900;
    letter-spacing: 4px;
    line-height: 1;
  }
  .card--front .brand-name {
    left: 60px;
    width: 350px;
    top: 300px;
    text-align: center;
    font-size: 78px;
    color: var(--brand-ink);
  }
  .info-rail {
    position: absolute;
    left: 444px;
    top: 0;
    width: 35px;
    height: 100%;
    background: var(--card-dark);
  }
  .info-tab {
    position: absolute;
    left: 428px;
    width: 66px;
    background: var(--card-dark);
    clip-path: polygon(0 0, 100% 0, 100% 78%, 78% 100%, 22% 100%, 0 78%);
    display: flex;
    align-items: center;
    justify-content: center;
  }
  .info-tab svg { width: 22px; height: 22px; fill: var(--white); }
  .info-tab--person { top: 106px; height: 54px; }
  .info-tab--phone { top: 170px; height: 60px; }
  .info-tab--web { top: 268px; height: 58px; }
  .info-tab--pin { top: 348px; height: 62px; }

  .contact { position: absolute; left: 520px; color: var(--ink); }
  .contact-name {
    top: 102px;
    font-size: 32px;
    letter-spacing: 0.5px;
    font-weight: 400;
    white-space: nowrap;
  }
  .contact-name strong { font-weight: 700; }
  .contact-role { top: 141px; font-size: 19px; color: var(--ink-soft); }
  .contact-phones { top: 192px; font-size: 21px; line-height: 25px; }
  .contact-web { top: 273px; font-size: 21px; line-height: 25px; }
  .contact-address { top: 364px; font-size: 16px; line-height: 20px; }

  /* Back */
  .card--back .brand-name {
    left: 0;
    width: 100%;
    top: 242px;
    text-align: center;
    font-size: 84px;
    color: var(--white);
  }
  .back-web {
    position: absolute;
    left: 0;
    width: 100%;
    top: 424px;
    display: flex;
    justify-content: center;
    align-items: center;
    gap: 8px;
    color: var(--white);
    font-size: 20px;
  }
  .back-web svg { width: 18px; height: 18px; }
</style>
</head>
<body>

<section class="card card--front" aria-label="Business card front">
  <div class="brand-name">VOMRA</div>

  <div class="info-rail"></div>
  <div class="info-tab info-tab--person">
    <svg viewBox="0 0 24 24"><circle cx="12" cy="7" r="4.5"/><path d="M3 22c0-5 4-8 9-8s9 3 9 8z"/></svg>
  </div>
  <div class="info-tab info-tab--phone">
    <svg viewBox="0 0 24 24"><path d="M6.6 10.8a15 15 0 0 0 6.6 6.6l2.2-2.2a1 1 0 0 1 1-.25 11.4 11.4 0 0 0 3.6.57 1 1 0 0 1 1 1V20a1 1 0 0 1-1 1A17 17 0 0 1 3 4a1 1 0 0 1 1-1h3.5a1 1 0 0 1 1 1c0 1.25.2 2.45.57 3.57a1 1 0 0 1-.25 1z"/></svg>
  </div>
  <div class="info-tab info-tab--web">
    <svg viewBox="0 0 24 24"><path d="M12 2a10 10 0 1 0 0 20 10 10 0 0 0 0-20zm-1 17.9A8 8 0 0 1 4 12l1 1 3 3v1a2 2 0 0 0 2 2zm6.9-2.5A2 2 0 0 0 16 16h-1v-3a1 1 0 0 0-1-1H8v-2h2a1 1 0 0 0 1-1V7h2a2 2 0 0 0 2-2v-.4a8 8 0 0 1 2.9 12.8z"/></svg>
  </div>
  <div class="info-tab info-tab--pin">
    <svg viewBox="0 0 24 24"><path d="M12 2a7 7 0 0 0-7 7c0 5.2 7 13 7 13s7-7.8 7-13a7 7 0 0 0-7-7zm0 9.5A2.5 2.5 0 1 1 12 6.5a2.5 2.5 0 0 1 0 5z"/></svg>
  </div>

  <p class="contact contact-name"><strong>DANIEL</strong> HARPER</p>
  <p class="contact contact-role">Solution Manager</p>
  <p class="contact contact-phones">+000 12345 6789<br>+000 12345 6789</p>
  <p class="contact contact-web">www.vomra.com.au<br>admin@vomra.com.au</p>
  <p class="contact contact-address">42-44 Harbour Lane Ridgeview<br>NSW 2050 Australia</p>
</section>

<section class="card card--back" aria-label="Business card back">
  <div class="brand-name">VOMRA</div>
  <p class="back-web">
    <svg viewBox="0 0 24 24" fill="none" stroke="#ffffff" stroke-width="1.8"><circle cx="12" cy="12" r="9.5"/><path d="M2.5 12h19M12 2.5c3 3 3 16 0 19M12 2.5c-3 3-3 16 0 19"/></svg>
    www.vomra.com.au
  </p>
</section>

</body>
</html>
```